Bork Ventures, Inc. Website redesign

Revamp the website, it is old and outdated. www.borkventuresinc.example

Target Market(s)

Information Technology Consulting and Staffing

Coding

Coded - Design and coding required

Number of Pages Required

5+ page

Colors

Designer to choose colors to be used in the design.

Requirements
Must have
• Outlined text boxes just like from the Tolvane.example site. A clean look

```html
<!DOCTYPE html>
<html lang="en">
<head>
<meta charset="utf-8">
<title>Bork Ventures, Inc.</title>
<link rel="stylesheet" href="https://fonts.googleapis.com/css2?family=Lato:wght@400;700;900&display=swap">
<style>
:root{
  --red:#8b0f2a;
  --dark:#2e2e2e;
  --ink:#222;
  --body:#444;
  --light:#f2f2f2;
  --white:#fff;
  --line:#cfcfcf;
}
*{margin:0;padding:0;box-sizing:border-box}
html,body{width:1200px;height:3056px;overflow:hidden}
body{position:relative;font-family:'Lato',sans-serif;color:var(--body);background:var(--white)}
.abs{position:absolute}
.topline{left:0;top:0;width:1200px;height:4px;background:#3a3a3a}
.phone-tab{left:858px;top:0;width:264px;height:47px;background:#3a3a3a;color:#fff;font-weight:700;font-size:21px;display:flex;align-items:center;justify-content:center;gap:12px;clip-path:polygon(0 0,100% 0,96% 100%,4% 100%)}
.logo{display:flex;align-items:center;gap:8px;font-weight:900;color:var(--ink);letter-spacing:1px}
.logo .mark{width:26px;height:26px;background:var(--red)}
.header-logo{left:75px;top:58px;font-size:26px}
.tagline{left:254px;top:64px;font-size:19px;color:#555;font-variant:small-caps;letter-spacing:.5px}
.nav{left:491px;top:84px;display:flex;align-items:center;height:35px}
.nav a{font-size:15px;font-weight:700;color:#333;text-decoration:none;margin-right:38px}
.nav a.active{background:var(--red);color:#fff;padding:0 16px;height:35px;line-height:35px;margin-right:22px}
.hero{left:0;top:139px;width:1200px;height:573px;background:radial-gradient(ellipse at 70% 45%,#2a4a78 0%,#1b2432 45%,#0f1217 100%)}
.hero h1{position:absolute;left:0;width:1200px;top:215px;text-align:center;color:#fff;font-size:92px;font-weight:900;line-height:1;letter-spacing:1px}
.hero h2{position:absolute;left:0;width:1200px;top:313px;text-align:center;color:#fff;font-size:35px;font-weight:900}
.dots{position:absolute;left:562px;top:524px;display:flex;gap:11px}
.dots span{width:11px;height:11px;border-radius:50%;background:#fff}
.dots span:first-child{background:var(--red)}
.sec-title{left:0;width:1200px;text-align:center;font-size:30px;font-weight:900;color:var(--ink)}
.card{top:836px;width:242px;height:254px;background:var(--dark);color:#fff;text-align:center;border-radius:0 0 8px 8px}
.card.featured{background:var(--red)}
.card svg{margin-top:36px}
.card h3{font-size:20px;font-weight:700;line-height:26px;margin-top:12px}
.card p{font-size:15px;line-height:21px;margin:14px 18px 0;color:#e6e6e6}
.band{left:0;width:1200px;height:383px;background:var(--light)}
.photo{background:linear-gradient(135deg,#1d2733,#4a5563 55%,#8a6a55)}
.h-sec{font-size:30px;font-weight:900;color:var(--ink)}
.sub{font-size:19px;font-weight:700;color:var(--red)}
.copy{font-size:15px;line-height:26px;color:var(--body)}
.btn{display:flex;align-items:center;justify-content:center;width:165px;height:46px;background:var(--red);color:#fff;font-size:15px;font-weight:700;border-radius:0 0 4px 4px}
.news{top:2032px;width:331px;height:353px;border:1px solid var(--line);background:#fff}
.news .img{height:185px;background:linear-gradient(135deg,#0e1c2e,#1d4f86 60%,#6fb3e6)}
.news h4{font-size:17px;font-weight:700;color:var(--ink);margin:22px 12px 0}
.news p{font-size:15px;line-height:23px;margin:8px 12px 0}
.news a{display:block;font-size:15px;font-weight:700;color:var(--red);margin:8px 12px 0;text-decoration:none}
.foot-h{font-size:15px;font-weight:700;color:var(--ink)}
.foot-list{font-size:14px;line-height:25px;color:#333}
.small{font-size:13px;line-height:19px;color:#555}
.social{display:flex;gap:18px}
.social span{width:20px;height:20px;background:#333;border-radius:3px}
.signup{display:flex}
.signup .field{width:201px;height:36px;border:1px solid #bbb;font-size:13px;color:#666;padding-left:14px;line-height:34px}
.signup .go{width:40px;height:36px;background:var(--red);color:#fff;font-size:13px;font-weight:700;text-align:center;line-height:36px}
</style>
</head>
<body>
<div class="abs topline"></div>
<div class="abs phone-tab">
  <svg width="18" height="18" viewBox="0 0 24 24"><path fill="#fff" d="M6.6 10.8a15 15 0 0 0 6.6 6.6l2.2-2.2c.3-.3.7-.4 1-.2 1.1.4 2.3.6 3.6.6.6 0 1 .4 1 1V20c0 .6-.4 1-1 1A17 17 0 0 1 3 4c0-.6.4-1 1-1h3.5c.6 0 1 .4 1 1 0 1.3.2 2.5.6 3.6.1.3 0 .7-.2 1z"/></svg>
  1-800-555-0147
</div>
<div class="abs logo header-logo"><span>BORK</span><span class="mark"></span></div>
<div class="abs tagline">Mission Integrity Results</div>
<nav class="abs nav">
  <a class="active">HOME</a><a>ABOUT US</a><a>SERVICES</a><a>STRATEGY</a><a>IT NEWS</a><a style="margin-right:0">CONTACT US</a>
</nav>

<section class="abs hero" role="img" aria-label="Close-up of network switch with blue patch cables and green port lights">
  <h1>BORK VENTURES</h1>
  <h2>MISSION INTEGRITY RESULTS</h2>
  <div class="dots"><span></span><span></span><span></span><span></span></div>
</section>

<h2 class="abs sec-title" style="top:768px">OUR SERVICES</h2>
<div class="abs card featured" style="left:75px">
  <svg width="64" height="46" viewBox="0 0 64 46"><rect x="10" y="3" width="44" height="30" rx="2" fill="none" stroke="#fff" stroke-width="4"/><rect x="2" y="37" width="60" height="5" rx="2" fill="#fff"/></svg>
  <h3>HARDWARE &amp;<br>SOFTWARE SALES</h3>
  <p>Sed accumsan sollicitudin sapien, sit amet adipiscing turpis gravida ac.</p>
</div>
<div class="abs card" style="left:343px">
  <svg width="64" height="52" viewBox="0 0 64 52"><circle cx="32" cy="12" r="9" fill="#fff"/><circle cx="13" cy="16" r="7" fill="#fff"/><circle cx="51" cy="16" r="7" fill="#fff"/><path d="M16 50c0-14 6-20 16-20s16 6 16 20z" fill="#fff"/><path d="M2 44c0-11 4-16 11-16 4 0 6 1 8 3-3 4-4 8-4 13z M62 44c0-11-4-16-11-16-4 0-6 1-8 3 3 4 4 8 4 13z" fill="#fff"/></svg>
  <h3>PROFESSIONAL<br>SERVICES</h3>
  <p>Sed accumsan sollicitudin sapien, sit amet adipiscing turpis gravida ac.</p>
</div>
<div class="abs card" style="left:614px">
  <svg width="60" height="52" viewBox="0 0 60 52"><circle cx="20" cy="28" r="13" fill="none" stroke="#fff" stroke-width="8" stroke-dasharray="5 3"/><circle cx="20" cy="28" r="5" fill="#fff"/><circle cx="46" cy="12" r="8" fill="none" stroke="#fff" stroke-width="5" stroke-dasharray="3 2"/><circle cx="46" cy="40" r="8" fill="none" stroke="#fff" stroke-width="5" stroke-dasharray="3 2"/></svg>
  <h3>TECHNOLOGY<br>ASSESSMENT</h3>
  <p>Sed accumsan sollicitudin sapien, sit amet adipiscing turpis gravida ac.</p>
</div>
<div class="abs card" style="left:884px">
  <svg width="60" height="50" viewBox="0 0 60 50"><ellipse cx="24" cy="19" rx="22" ry="16" fill="#fff"/><path d="M8 30l-4 10 12-6z" fill="#fff"/><ellipse cx="40" cy="30" rx="18" ry="13" fill="#fff" stroke="#2e2e2e" stroke-width="3"/><path d="M50 40l6 8-12-5z" fill="#fff"/></svg>
  <h3>TECHNOLOGY<br>CONSULTING</h3>
  <p>Sed accumsan sollicitudin sapien, sit amet adipiscing turpis gravida ac.</p>
</div>

<section class="abs band" style="top:1153px">
  <div class="abs photo" style="left:585px;top:0;width:615px;height:383px;clip-path:polygon(0 0,100% 0,100% 100%,68px 100%)" role="img" aria-label="Technician working at a laptop beside server racks"></div>
  <h2 class="abs h-sec" style="left:75px;top:60px">WELCOME TO BORK VENTURES</h2>
  <p class="abs sub" style="left:75px;top:112px">Bringing Thought Leadership and Quality to Every Project</p>
  <p class="abs copy" style="left:75px;top:143px;width:500px">Bork Ventures, Inc. is an 8(a) full-service IT consulting company based in the Washington, DC Metro area. We offer specialized, highly customized technology solutions for our customers located throughout<br>the United States.</p>
  <div class="abs btn" style="left:75px;top:269px">READ MORE</div>
</section>

<section class="abs band" style="top:1536px;background:var(--light)">
  <div class="abs photo" style="left:0;top:0;width:584px;height:383px;clip-path:polygon(0 0,510px 0,100% 100%,0 100%);background:linear-gradient(135deg,#c9c2b8,#8a8278 50%,#3e3a36)" role="img" aria-label="Smiling team of business professionals standing together in an office"></div>
  <h2 class="abs h-sec" style="left:635px;top:64px">OUR LEADERS</h2>
  <p class="abs copy" style="left:635px;top:114px;width:490px">BVI is a global risk management firm providing unmatched client value. Our expertise and capabilities enables us to support clients worldwide. Whether the issue, risk or threat impacts your people, property &amp;<br>&nbsp;operations, products, intellectual property or reputation BVI has the resources and expertise to support your needs.</p>
  <div class="abs btn" style="left:635px;top:273px">OUR TEAM</div>
</section>

<h2 class="abs sec-title" style="top:1968px">LATEST NEWS</h2>
<article class="abs news" style="left:75px">
  <div class="img" role="img" aria-label="Rack-mounted patch panels with blue network cables"></div>
  <h4>CONSECTETUER ADIPISCING ELIT</h4>
  <p>Aliquam molestie, mi et imperdiet euismod, dui purus auctor tellus, etinterdum lacus lectus aliquam erat volutpat.</p>
  <a>[Read More]</a>
</article>
<article class="abs news" style="left:434px">
  <div class="img" role="img" aria-label="Hand holding a glowing laptop with digital network icons"></div>
  <h4>CONSECTETUER ADIPISCING ELIT</h4>
  <p>Aliquam molestie, mi et imperdiet euismod, dui purus auctor tellus, etinterdum lacus lectus aliquam erat volutpat.</p>
  <a>[Read More]</a>
</article>
<article class="abs news" style="left:794px">
  <div class="img" style="background:linear-gradient(135deg,#cfd6dc,#8f9ba6 50%,#c4a27a)" role="img" aria-label="Engineer with tablet checking cables in a server cabinet"></div>
  <h4>CONSECTETUER ADIPISCING ELIT</h4>
  <p>Aliquam molestie, mi et imperdiet euismod, dui purus auctor tellus, etinterdum lacus lectus aliquam erat volutpat.</p>
  <a>[Read More]</a>
</article>

<section class="abs band" style="top:2419px">
  <div class="abs photo" style="left:584px;top:0;width:616px;height:383px;clip-path:polygon(76px 0,100% 0,100% 100%,0 100%);background:linear-gradient(135deg,#0c1220,#16335e 55%,#2f6fb8)" role="img" aria-label="Two IT specialists walking through a data center with a tablet"></div>
  <h2 class="abs h-sec" style="left:75px;top:56px">OUR STRATEGY</h2>
  <p class="abs sub" style="left:75px;top:105px">Our Strategy: Your Path to Success</p>
  <p class="abs copy" style="left:75px;top:135px;width:525px">Civilian and Federal agencies are facing increased demands driven by the changing economic environment and shifts in the way products and services are sold and delivered.. These factors have created an imperative to leverage new and innovative technology solution<br>architectures.</p>
  <div class="abs btn" style="left:75px;top:283px">READ MORE</div>
</section>

<footer>
  <div class="abs logo" style="left:75px;top:2863px;font-size:34px"><span>BORK</span><span class="mark" style="width:34px;height:34px"></span></div>
  <p class="abs small" style="left:75px;top:2925px">Copyright © 2019. Company Name.<br>All Right Reserved</p>
  <div class="abs social" style="left:75px;top:2990px" aria-label="Social links"><span></span><span></span><span></span><span></span><span></span></div>

  <h3 class="abs foot-h" style="left:381px;top:2854px">SITE MAP</h3>
  <ul class="abs foot-list" style="left:381px;top:2877px;list-style:none">
    <li>Home</li><li>About us</li><li>Services</li><li>Strategy</li><li>IT News</li><li>Contact us</li>
  </ul>

  <h3 class="abs foot-h" style="left:597px;top:2854px">CONTACT INFO</h3>
  <p class="abs foot-list" style="left:597px;top:2880px;line-height:22px"><strong style="color:var(--red)">Bork Ventures, Inc.</strong><br>2280 Larkhollow Dr<br>Fenwick, MD 20999</p>
  <p class="abs foot-list" style="left:597px;top:2952px;line-height:29px">
    <svg width="12" height="12" viewBox="0 0 24 24"><path fill="#333" d="M6.6 10.8a15 15 0 0 0 6.6 6.6l2.2-2.2c.3-.3.7-.4 1-.2 1.1.4 2.3.6 3.6.6.6 0 1 .4 1 1V20c0 .6-.4 1-1 1A17 17 0 0 1 3 4c0-.6.4-1 1-1h3.5c.6 0 1 .4 1 1 0 1.3.2 2.5.6 3.6.1.3 0 .7-.2 1z"/></svg>&nbsp;&nbsp;&nbsp;&nbsp;301-555-0192<br>
    <svg width="13" height="10" viewBox="0 0 26 20"><rect width="26" height="20" fill="#333"/><path d="M1 1l12 10L25 1" fill="none" stroke="#fff" stroke-width="2"/></svg>&nbsp;&nbsp;&nbsp;&nbsp;info@borkventures.example
  </p>

  <h3 class="abs foot-h" style="left:884px;top:2854px">EMAIL SIGN UP</h3>
  <div class="abs signup" style="left:884px;top:2896px"><div class="field">Enter Email Address</div><div class="go">GO</div></div>
</footer>
</body>
</html>
```